Catering Menu Package

I currently have a complete menu package, which we have redesigned as far as content, now I need to it put together in a catalog type format. It is essentially 10-12 pages in length, and will be sent for print production. Upon receiving a final edit
Updates

I have added an example gif to the project.

I did this free hand this basically what I am looking for. please change text and type to whatever you think would look best. This is a total rough design so, feel free to change any and everything. The text for the page is on the word documents. If you need more images let me know I am in the process of getting as many images uploaded for your use.

Project Deadline Extended
Reason: I figured we got a late jump with questions, so i am extending a few days .

Target Market(s)

The target market is business who wish to have catered luncheons, breakfasts , meetings

Industry/Entity Type

Catering

Requirements
Must have
• I have attached a copy of the text that what we want in the package, our logo, and i have also attached a catering package of another company to give you an idea what the finished product will be
Should not have
• It should not look identical to the example catering packages, these are for some inspiration we want our own design with the same type of look and feel

```html
<!DOCTYPE html>
<html lang="en">
<head>
<meta charset="utf-8">
<title>Desserts Menu</title>
<link rel="stylesheet" href="https://fonts.googleapis.com/css2?family=Lora:ital,wght@0,400;1,600;1,700&family=Italianno&display=swap">
<style>
:root {
  --page: #ffffff;
  --side-strip: #e4d9d3;
  --side-fade: #f3eeeb;
  --title: #c8175f;
  --body: #5c4c44;
  --heading: #6e5e55;
  --brand: #231f1d;
  --cookie: #c9a27a;
  --cookie-dark: #9a7350;
  --petit: #7a1a1e;
  --petit-light: #e9dcc0;
  --fountain: #5a3522;
  --fountain-light: #c89a6a;
}
* { margin: 0; padding: 0; box-sizing: border-box; }
html, body { width: 1200px; height: 927px; overflow: hidden; }
body {
  position: relative;
  font-family: "Lora", Georgia, serif;
  color: var(--body);
  background:
    radial-gradient(ellipse 700px 420px at 185px 0, var(--side-fade) 0%, rgba(255,255,255,0) 70%),
    linear-gradient(to right, var(--side-strip) 0, #ece4df 150px, var(--side-fade) 184px, var(--page) 186px);
}
.brand {
  position: absolute;
  left: 28px; top: 30px;
  width: 135px;
  text-align: center;
  color: var(--brand);
  font-family: "Lora", Georgia, serif;
  font-weight: 400;
  font-size: 21px;
  line-height: 1.15;
}
.brand-mark {
  width: 110px; height: 110px;
  margin: 0 auto 22px;
  border: 3px solid var(--brand);
}
.page-heading {
  position: absolute;
  left: 200px; top: 52px;
  font-family: "Italianno", cursive;
  font-weight: 400;
  font-size: 48px;
  color: var(--heading);
  line-height: 1;
}
.menu { position: absolute; left: 197px; top: 0; width: 970px; }
.menu p, .menu h2 { position: absolute; left: 0; white-space: nowrap; }
.item-title {
  font-style: italic;
  font-weight: 700;
  font-size: 20px;
  color: var(--title);
  line-height: 1;
}
.item-text { font-size: 17.5px; line-height: 24px; }
.price {
  position: absolute;
  left: 800px;
  font-size: 17px;
  white-space: nowrap;
}
.photo { position: absolute; display: block; }
</style>
</head>
<body>
  <div class="brand">
    <div class="brand-mark"></div>
    Willow<br>Lane<br>Kitchens
  </div>

  <h1 class="page-heading">Desserts</h1>

  <section class="menu">
    <h2 class="item-title" style="top:119px">Homemade Cookies, Brownies &amp; Blondies</h2>
    <span class="price" style="top:121px">$XX.XX per person</span>

    <h2 class="item-title" style="top:167px">Dessert Miniatures</h2>
    <p class="item-text" style="top:212px">Homemade Cookies, Brownies, Blondies, Petit Fours</p>

    <p class="item-text" style="top:261px">Miniature Chocolate Mousse Cups &amp; Crème Puffs</p>
    <span class="price" style="top:264px">$XX.XX per person</span>

    <p class="item-text" style="top:309px">Strawberry Shortcake &amp; Chocolate Brownie Mousse Parfaits</p>
    <span class="price" style="top:312px">$XX.XX per person</span>

    <h2 class="item-title" style="top:361px">New York Style Cheesecake Bar</h2>
    <p class="item-text" style="top:382px">With warm chocolate sauce, caramel, strawberries<br>Cherries &amp; whipped topping</p>
    <span class="price" style="top:410px">$XX.XX per person</span>

    <h2 class="item-title" style="top:458px">Ice Cream Sundae Bar</h2>
    <p class="item-text" style="top:479px">Hand Dipped Ice Cream Cups. Served With Toppings:Chopped Nuts, Chocolate Chips,<br>Crushed Cocoa Cookies,Rainbow Sprinkles, Cherries, Whipped Topping,Chocolate Syrup,<br>Caramel, Pineapple, Strawberry</p>

    <h2 class="item-title" style="top:578px">Chocolate Fountain</h2>
    <p class="item-text" style="top:600px">Milk Chocolate, Dark Chocolate Or White Chocolate. Marshmallows, Fresh Strawberries,<br>Bananas, Pineapple,Cookies, Rice Crispy Treats, Pretzels, Angel Cake, Pound Cake</p>
  </section>

  <svg class="photo" style="left:185px;top:690px" width="404" height="237" viewBox="0 0 404 237" role="img" aria-label="Photo of a pile of chocolate chip cookies">
    <defs>
      <linearGradient id="cookieFill" x1="0" y1="0" x2="1" y2="1">
        <stop offset="0" stop-color="#d8b48c"/>
        <stop offset="0.6" stop-color="var(--cookie)"/>
        <stop offset="1" stop-color="var(--cookie-dark)"/>
      </linearGradient>
    </defs>
    <path d="M0 12 C120 30 260 0 404 22 L404 237 L0 237 Z" fill="url(#cookieFill)"/>
  </svg>

  <svg class="photo" style="left:598px;top:628px" width="362" height="299" viewBox="0 0 362 299" role="img" aria-label="Photo of a platter of holiday petit fours">
    <defs>
      <linearGradient id="petitFill" x1="0" y1="0" x2="1" y2="1">
        <stop offset="0" stop-color="var(--petit-light)"/>
        <stop offset="0.5" stop-color="#a3383a"/>
        <stop offset="1" stop-color="var(--petit)"/>
      </linearGradient>
    </defs>
    <path d="M0 46 C110 60 240 40 362 0 L362 299 L0 299 Z" fill="url(#petitFill)"/>
  </svg>

  <svg class="photo" style="left:967px;top:606px" width="233" height="321" viewBox="0 0 233 321" role="img" aria-label="Photo of a chocolate fountain with fruit at a buffet">
    <defs>
      <linearGradient id="fountainFill" x1="0" y1="0" x2="0" y2="1">
        <stop offset="0" stop-color="var(--fountain-light)"/>
        <stop offset="0.5" stop-color="var(--fountain)"/>
        <stop offset="1" stop-color="#6f6a2e"/>
      </linearGradient>
    </defs>
    <path d="M0 20 C80 2 160 0 233 4 L233 321 L0 321 Z" fill="url(#fountainFill)"/>
  </svg>
</body>
</html>
```